4D Cradle Glimpse Luxury Ultrasound Billboard

Design a HIGH-END, MODERN billboard for my private prenatal ultrasound studio, 4D Cradle Glimpse, located in Linden Cove.
This billboard will be viewed by drivers traveling at highway speeds, so it must be extremely clean, simple, and readable within 6 seconds.
About My Business
4D Cradle Glimpse is a private prenatal ultrasound studio specializing in:
Highest technology 4D/HD Ultrasounds
Early Gender Determination
Pregnancy Confirmation
I have been serving families for nearly 10 years and is known for creating a memorable experience, not just an ultrasound appointment.
Design Style
I DO NOT want:
Flowers
Leaves
Swirls
Glitter
Hearts everywhere
Busy backgrounds
Generic maternity stock graphics
I DO want:
Modern
Luxury
Upscale
Clean
Professional
Eye-catching
Premium medical spa feel
Colors
Use colors from my logo:
LOGO Green ( or a deep green)
Black
White
Soft Gold accents
Images:
Incorporate my professional headshot in a clean, modern way, logo, and the ultrasound images
Text
Keep wording minimal.
Primary Headline ( OPEN TO IDEAS) :
EXAMPLES ( WOULD RATHER SOMETHING MORE CATCHY)
" ADVANCED IMAGING. UNFORGETTABLE MOMENTS"
"MEET YOUR BABY BEFORE BIRTH"
Under headline:
4D Ultrasound • Early Gender • Pregnancy Confirmation
Business Name:
4D Cradle Glimpse
Private Prenatal Ultrasound Studio
Phone Number:
850-471-5923
Important
This billboard must be readable in 5–6 seconds from a moving vehicle.
Less text is better.
The phone number and business name must be visible from a distance.
The design should feel like a premium brand that immediately tells expecting parents:
“This is where I go to see my baby.”
Files Provided
Official logo
Headshot
Ultrasound images
Don’t make this look like a medical office billboard.
Make it look like a luxury baby experience billboard. That’s what separates 4D Cradle Glimpse from hospitals, OB offices, and all the new studios popping up around you. The emotional connection is what gets moms to book. ❤️
Billboard Size - 10.6” x 36”

```html
<!DOCTYPE html>
<html lang="en">
<head>
<meta charset="utf-8">
<title>4D Cradle Glimpse Billboard</title>
<link rel="stylesheet" href="https://fonts.googleapis.com/css2?family=Josefin+Sans:wght@400;600;700&family=Allura&display=swap">
<style>
  :root {
    --green: #1f3a2c;
    --green-deep: #162b20;
    --cream: #f5f2ec;
    --gold: #c9a052;
    --gold-light: #e2c27a;
    --ink: #1d2a23;
    --white: #ffffff;
  }
  html, body {
    margin: 0;
    width: 1088px;
    height: 1200px;
    overflow: hidden;
    background: #ffffff;
  }
  .billboard {
    position: absolute;
    left: 24px;
    top: 352px;
    width: 1243px;
    height: 592px;
    transform: scale(0.8367);
    transform-origin: top left;
    font-family: "Josefin Sans", sans-serif;
    overflow: hidden;
    box-shadow: 0 6px 20px rgba(0,0,0,.18);
  }
  .billboard-shapes { position: absolute; inset: 0; }
  .brand-name {
    position: absolute;
    left: 300px; width: 645px;
    top: 70px;
    margin: 0;
    text-align: center;
    color: var(--green);
    font-weight: 700;
    line-height: 1;
  }
  .brand-name .line-one { display: block; font-size: 96px; }
  .brand-name .line-two { display: block; font-size: 68px; margin-top: 6px; }
  .studio-tagline {
    position: absolute;
    left: 300px; width: 645px;
    top: 316px;
    margin: 0;
    text-align: center;
    font-size: 21px;
    letter-spacing: 2.6px;
    color: var(--ink);
  }
  .service {
    position: absolute;
    top: 397px;
    font-size: 15.5px;
    letter-spacing: 0.8px;
    line-height: 21px;
    color: var(--ink);
    text-transform: uppercase;
    font-weight: 400;
    white-space: nowrap;
  }
  .service-one { left: 406px; }
  .service-two { left: 632px; }
  .service-three { left: 814px; }
  .phone-number {
    position: absolute;
    left: 243px; top: 478px;
    width: 360px;
    margin: 0;
    text-align: center;
    font-size: 52px;
    font-weight: 600;
    letter-spacing: 3px;
    color: var(--white);
    white-space: nowrap;
  }
  .location {
    position: absolute;
    left: 243px; top: 541px;
    width: 360px;
    display: flex;
    align-items: center;
    gap: 14px;
    font-size: 19px;
    letter-spacing: 3px;
    color: var(--gold);
    font-weight: 600;
    white-space: nowrap;
  }
  .location::before, .location::after {
    content: "";
    flex: 1;
    height: 1.5px;
    background: var(--gold);
  }
  .slogan-script {
    position: absolute;
    left: 712px; top: 480px;
    font-family: "Allura", cursive;
    font-size: 36px;
    color: var(--white);
  }
  .slogan-caps {
    position: absolute;
    left: 712px; top: 527px;
    font-size: 19.5px;
    letter-spacing: 2.2px;
    font-weight: 600;
    color: var(--gold);
  }
</style>
</head>
<body>
<div class="billboard">
  <svg class="billboard-shapes" viewBox="0 0 1243 592" width="1243" height="592">
    <defs>
      <linearGradient id="headshotTone" x1="0" y1="0" x2="0" y2="1">
        <stop offset="0" stop-color="#213c2e"/>
        <stop offset="0.5" stop-color="#3c5242"/>
        <stop offset="1" stop-color="#1f3526"/>
      </linearGradient>
      <radialGradient id="babyTone" cx="0.55" cy="0.45" r="0.7">
        <stop offset="0" stop-color="#b07a52"/>
        <stop offset="0.6" stop-color="#7a4a2c"/>
        <stop offset="1" stop-color="#3a2114"/>
      </radialGradient>
      <linearGradient id="goldSheen" x1="0" y1="0" x2="1" y2="1">
        <stop offset="0" stop-color="#b88b3c"/>
        <stop offset="0.5" stop-color="#f0d592"/>
        <stop offset="1" stop-color="#b88b3c"/>
      </linearGradient>
    </defs>

    <rect class="panel-cream" x="0" y="0" width="1243" height="467" fill="var(--cream)"/>

    <path role="img" aria-label="Sepia 4D ultrasound image of a sleeping baby with hands near its face"
          d="M975,0 L1243,0 L1243,467 L945,467 C1030,330 1035,150 975,0 Z" fill="url(#babyTone)"/>
    <path d="M975,0 C1035,150 1030,330 945,467" fill="none" stroke="url(#goldSheen)" stroke-width="5"/>

    <path d="M0,0 L275,0 C228,150 220,330 310,467 L0,467 Z" fill="var(--green)"/>
    <path role="img" aria-label="Professional headshot of the studio owner in green scrubs holding an ultrasound probe"
          d="M0,0 L262,0 C216,150 208,330 292,467 L0,467 Z" fill="url(#headshotTone)"/>
    <path d="M275,0 C228,150 220,330 310,467" fill="none" stroke="url(#goldSheen)" stroke-width="5"/>

    <rect x="300" y="45" width="645" height="323" rx="30" fill="#fbfaf6" stroke="url(#goldSheen)" stroke-width="7"/>
    <rect x="309" y="54" width="627" height="305" rx="24" fill="none" stroke="var(--green)" stroke-width="1.5"/>
    <line x1="345" y1="290" x2="900" y2="290" stroke="var(--gold)" stroke-width="2"/>

    <g fill="none" stroke="var(--gold)" stroke-width="2">
      <circle cx="367" cy="416" r="28"/>
      <circle cx="592" cy="416" r="28"/>
      <circle cx="775" cy="416" r="28"/>
    </g>
    <g fill="none" stroke="var(--green)" stroke-width="2.2">
      <rect x="354" y="403" width="26" height="18" rx="2"/>
      <path d="M360,417 Q367,406 374,417"/>
      <line x1="352" y1="427" x2="382" y2="427"/>
      <circle cx="587" cy="414" r="8"/>
      <line x1="587" y1="422" x2="587" y2="433"/>
      <line x1="582" y1="428" x2="592" y2="428"/>
      <circle cx="597" cy="419" r="8"/>
      <line x1="602" y1="413" x2="609" y2="404"/>
      <path d="M603,404 L609,404 L609,410"/>
      <path d="M775,430 C758,418 761,403 769,404 C773,405 775,408 775,410 C775,408 777,405 781,404 C789,403 792,418 775,430 Z"/>
    </g>
    <g stroke="var(--gold)" stroke-width="1.5">
      <line x1="548" y1="396" x2="548" y2="436"/>
      <line x1="727" y1="396" x2="727" y2="436"/>
    </g>

    <rect x="0" y="467" width="1243" height="125" fill="var(--green-deep)"/>
    <line x1="0" y1="468" x2="1243" y2="468" stroke="url(#goldSheen)" stroke-width="4"/>
    <circle cx="192" cy="516" r="33" fill="none" stroke="var(--gold)" stroke-width="2.5"/>
    <path d="M181,500 L187,498 L192,508 L188,512 C190,518 194,522 199,524 L203,520 L212,525 L210,532 C196,535 176,516 181,500 Z" fill="var(--gold)"/>
    <g stroke="var(--gold)" stroke-width="1.5">
      <line x1="675" y1="486" x2="675" y2="568"/>
      <line x1="712" y1="566" x2="865" y2="566"/>
      <line x1="910" y1="566" x2="1086" y2="566"/>
    </g>
    <path d="M887,574 C876,566 878,558 883,558 C885,558 887,560 887,561 C887,560 889,558 891,558 C896,558 898,566 887,574 Z" fill="var(--gold)"/>
  </svg>

  <h1 class="brand-name"><span class="line-one">4D</span><span class="line-two">Cradle Glimpse</span></h1>
  <p class="studio-tagline">PRIVATE PRENATAL ULTRASOUND STUDIO</p>

  <div class="service service-one">4D/HD<br>Ultrasound</div>
  <div class="service service-two">Early<br>Gender</div>
  <div class="service service-three">Pregnancy<br>Confirmation</div>

  <p class="phone-number">850-471-5923</p>
  <div class="location">LINDEN COVE</div>
  <div class="slogan-script">More than an ultrasound.</div>
  <div class="slogan-caps">A MEMORY THAT LASTS A LIFETIME.</div>
</div>
</body>
</html>
```